Cocktail-Making Assistant App re-design

Ok boys and girls, here's the deal:
I have an android app which is almost complete, but needs a design overhaul.

The app is a standard cocktail-making assistant: gives you a list of cocktails and the ability to see which cocktail you can make out of those ingredients (drinks, fruit, etc) you have at home.

I've attached some general app flow, as well as detailed requirements/explanation presentation. Most of those things are just FYI, so that you know what it's about.

3 screens are the most important (main screen, cocktail view screen, ingredient view screen), meaning I will pick the design mostly based on ideas for those 3 things, with the fourth being a rather simple list (given on attached flow, third tier)
Some other screens are derived from that, with some minor changes on it, but you shouldn't care about that.

There are lots of other, non-explained things which I said nothing about only because they are (from design point of view) completely the same and would only make it seem more complicated.

I don't want to influence the colour scheme, but the app will be released under RedFig developer name (having a light colured red fig as a logo) so I suppose some brownish design, for example, will not really fit nicely. If you, however, have a killer which you are confident will prove me wrong, I'm looking forward to seeing it!

It should be a serious, elegant look (as opposed to cartoonish, but we are not aiming for a business look at all!), not cluttered with details, no clubbing themes, glitter and so on.

Test apk file available on request (Android 2.3+).

Edit: payment is now guaranteed
Also please note that currently, the favorite, "heart" button has a motion effect:
on click it flies out of the screen to the left (white heart) and comes back to the screen as a red heart. Take that into consideration, if it means anything to you.

Target Market(s)

Whoever you imagine would enjoy drinking cocktails

Industry/Entity Type

Business

Requirements
Must have
• Everything is said in the provided documentation - images say more than I could possibly write here.
Nice to have
• As said, most of the icons are a nice-to-have. Only those which are critically linked to the rest of the design must be provided. More details in the docs.
Should not have
• No cartoon look, No zillion colours

```html
<!DOCTYPE html>
<html lang="en">
<head>
<meta charset="utf-8">
<title>Cocktail Search</title>
<link rel="stylesheet" href="https://fonts.googleapis.com/css2?family=Michroma&display=swap">
<style>
  :root {
    --bg: #f7f7f7;
    --header-top: #ffffff;
    --header-bottom: #ececec;
    --ink: #111111;
    --muted: #6f6f74;
    --rule: #b9b9b9;
    --search-bg: #dedbe0;
    --accent-red: #d81f2a;
    --accent-red-dark: #8e0f16;
    --star-green: #9ccc5a;
    --star-orange: #f6b94a;
    --star-red: #ef4f5e;
    --star-lilac: #b4aef0;
    --star-rose: #d9b3a6;
    --star-off: #2a2a2a;
  }
  * { box-sizing: border-box; margin: 0; padding: 0; }
  html, body { width: 676px; height: 1200px; overflow: hidden; }
  body {
    background: var(--bg);
    font-family: "Michroma", sans-serif;
    color: var(--ink);
    position: relative;
  }
  .app-header {
    position: absolute; left: 0; top: 0; width: 676px; height: 97px;
    background: linear-gradient(var(--header-top), var(--header-bottom));
  }
  .home-button { position: absolute; left: 10px; top: 18px; width: 80px; height: 60px; }
  .header-divider { position: absolute; left: 131px; top: 14px; width: 1px; height: 74px; background: #d4d4d4; }
  .screen-title {
    position: absolute; left: 163px; top: 38px;
    font-size: 22px; letter-spacing: 1.5px; text-transform: uppercase;
  }
  .header-band {
    position: absolute; left: 0; top: 97px; width: 676px; height: 10px;
    background: linear-gradient(var(--accent-red), var(--accent-red-dark));
  }
  .search-bar {
    position: absolute; left: 64px; top: 117px; width: 546px; height: 41px;
    border-radius: 21px; background: var(--search-bg);
  }
  .search-label {
    position: absolute; left: 144px; top: 13px;
    font-size: 14px; letter-spacing: 1.5px; color: var(--muted); text-transform: uppercase;
  }
  .search-icon { position: absolute; right: 42px; top: 6px; width: 30px; height: 30px; }
  .cocktail-list { position: absolute; left: 0; top: 182px; width: 676px; list-style: none; }
  .cocktail-row {
    position: relative; height: 169px;
    border-top: 1px solid var(--rule);
  }
  .cocktail-image {
    position: absolute; top: 18px; width: 118px; height: 134px; border-radius: 6px;
  }
  .cocktail-info {
    position: absolute; left: 303px; top: 0; width: 240px; height: 169px;
    display: flex; flex-direction: column; justify-content: center; gap: 14px;
  }
  .cocktail-name {
    font-size: 16px; line-height: 23px; letter-spacing: 1px; text-transform: uppercase;
  }
  .rating { display: flex; gap: 8px; }
  .rating svg { width: 34px; height: 34px; }
  .row-divider { position: absolute; left: 545px; top: 42px; width: 1px; height: 84px; background: #d0d0d0; }
  .stock {
    position: absolute; left: 558px; top: 44px; width: 76px; text-align: center;
    font-size: 11px; line-height: 14px; text-transform: uppercase;
  }
  .stock svg { width: 28px; height: 42px; display: block; margin: 0 auto 6px; }
  .g { fill: var(--star-green); } .o { fill: var(--star-orange); } .r { fill: var(--star-red); }
  .l { fill: var(--star-lilac); } .p { fill: var(--star-rose); } .d { fill: var(--star-off); }
</style>
</head>
<body>
<svg width="0" height="0" style="position:absolute">
  <defs>
    <symbol id="star" viewBox="0 0 24 24"><path d="M12 1.5l3.1 7.3 7.9.6-6 5.2 1.8 7.7L12 18.2l-6.8 4.1L7 14.6 1 9.4l7.9-.6z"/></symbol>
    <symbol id="shaker" viewBox="0 0 28 42">
      <rect x="10" y="0" width="8" height="4" rx="2"/>
      <path d="M6 5h16l2 9H4z"/>
      <path d="M3 15h22l-3 27H6z"/>
    </symbol>
  </defs>
</svg>

<header class="app-header">
  <svg class="home-button" viewBox="0 0 80 60" aria-label="Back to home">
    <path d="M14 18l-9 10 9 10" fill="none" stroke="#d81f2a" stroke-width="3"/>
    <path d="M50 4l26 24h-8v28H56V40H44v16H32V28h-8z" fill="#111"/>
    <rect x="62" y="8" width="6" height="12" fill="#111"/>
  </svg>
  <div class="header-divider"></div>
  <h1 class="screen-title">Cocktail Search</h1>
</header>
<div class="header-band"></div>

<div class="search-bar">
  <span class="search-label">Search All</span>
  <svg class="search-icon" viewBox="0 0 30 30" aria-hidden="true">
    <circle cx="12" cy="12" r="8" fill="none" stroke="#333" stroke-width="3"/>
    <path d="M18 18l9 9" stroke="#333" stroke-width="5" stroke-linecap="round"/>
  </svg>
</div>

<ul class="cocktail-list">
  <li class="cocktail-row">
    <div class="cocktail-image" role="img" aria-label="Group of colourful cocktails with orange slices" style="left:96px;width:150px;background:linear-gradient(135deg,#f7c43c,#e9862b 45%,#8a3b1e)"></div>
    <div class="cocktail-info">
      <div class="cocktail-name">'57 Cruiser</div>
      <div class="rating"><svg class="g"><use href="#star"/></svg><svg class="o"><use href="#star"/></svg><svg class="r"><use href="#star"/></svg><svg class="l"><use href="#star"/></svg><svg class="p"><use href="#star"/></svg></div>
    </div>
    <div class="row-divider"></div>
    <div class="stock"><svg><use href="#shaker"/></svg>Have<br>0 of 4</div>
  </li>
  <li class="cocktail-row">
    <div class="cocktail-image" role="img" aria-label="Tulip glass with a pale golden spirit" style="left:126px;width:64px;background:linear-gradient(#f1f1f1 40%,#e8dca0 60%,#cfcfcf)"></div>
    <div class="cocktail-info">
      <div class="cocktail-name">'57 Cruiser #2</div>
      <div class="rating"><svg class="g"><use href="#star"/></svg><svg class="o"><use href="#star"/></svg><svg class="r"><use href="#star"/></svg><svg class="l"><use href="#star"/></svg><svg class="d"><use href="#star"/></svg></div>
    </div>
    <div class="row-divider"></div>
    <div class="stock"><svg><use href="#shaker"/></svg>Have<br>0 of 4</div>
  </li>
  <li class="cocktail-row">
    <div class="cocktail-image" role="img" aria-label="Tall glass with a pink red drink" style="left:130px;width:68px;background:linear-gradient(#f4f4f4 10%,#f26a7e 20%,#e0334f)"></div>
    <div class="cocktail-info" style="top:12px">
      <div class="cocktail-name">'57 Cruiser with a white license plate</div>
      <div class="rating"><svg class="g"><use href="#star"/></svg><svg class="o"><use href="#star"/></svg><svg class="r"><use href="#star"/></svg><svg class="d"><use href="#star"/></svg><svg class="d"><use href="#star"/></svg></div>
    </div>
    <div class="row-divider"></div>
    <div class="stock"><svg><use href="#shaker"/></svg>Have<br>0 of 4</div>
  </li>
  <li class="cocktail-row">
    <div class="cocktail-image" role="img" aria-label="Wine glass with a deep red drink and a strawberry" style="left:132px;width:60px;background:linear-gradient(#d8303b,#b3121d 55%,#e6e6e6 60%)"></div>
    <div class="cocktail-info">
      <div class="cocktail-name">1-900-MIX-MEUP</div>
      <div class="rating"><svg class="g"><use href="#star"/></svg><svg class="o"><use href="#star"/></svg><svg class="d"><use href="#star"/></svg><svg class="d"><use href="#star"/></svg><svg class="d"><use href="#star"/></svg></div>
    </div>
    <div class="row-divider"></div>
    <div class="stock"><svg><use href="#shaker"/></svg>Have<br>0 of 4</div>
  </li>
  <li class="cocktail-row">
    <div class="cocktail-image" role="img" aria-label="Tumbler with a green drink and fresh herbs" style="left:132px;width:70px;background:linear-gradient(#5c9a2e,#a6c63a 30%,#8fb22c 85%,#e0e0e0)"></div>
    <div class="cocktail-info">
      <div class="cocktail-name">110 in the Shade</div>
      <div class="rating"><svg class="g"><use href="#star"/></svg><svg class="d"><use href="#star"/></svg><svg class="d"><use href="#star"/></svg><svg class="d"><use href="#star"/></svg><svg class="d"><use href="#star"/></svg></div>
    </div>
    <div class="row-divider"></div>
    <div class="stock"><svg><use href="#shaker"/></svg>Have<br>0 of 4</div>
  </li>
  <li class="cocktail-row">
    <div class="cocktail-image" role="img" aria-label="Tall glass with a bright blue drink and a lime slice" style="left:146px;width:56px;background:linear-gradient(#a8e04a,#3fb7e8 20%,#1583cf 85%,#e0e0e0)"></div>
    <div class="cocktail-info">
      <div class="cocktail-name" style="line-height:28px">151 Florida Bushwacker</div>
      <div class="rating"><svg class="d"><use href="#star"/></svg><svg class="d"><use href="#star"/></svg><svg class="d"><use href="#star"/></svg><svg class="d"><use href="#star"/></svg><svg class="d"><use href="#star"/></svg></div>
    </div>
    <div class="row-divider"></div>
    <div class="stock"><svg><use href="#shaker"/></svg>Have<br>0 of 4</div>
  </li>
</ul>
</body>
</html>
```